Calderwell Climate Business Card Design

Design new, 2 sides, business cards for a residential and light commercial heating, air conditioning contractor.

Target Market(s)

Homeowners, small businesses

Industry/Entity Type

Business

Contact Information for Business Card

Dominic Westerhall
Phone - 862-415-2736
Email
Address - PO box 518
Brightwater NJ 07912
Website - www.HarborBreezeLLC.example

Requirements
Must have
• logo, company colors, standard size with no die cut, so I can use nova stamp

```html
<!DOCTYPE html>
<html lang="en">
<head>
<meta charset="utf-8">
<title>Calderwell Climate Business Card</title>
<link rel="stylesheet" href="https://fonts.googleapis.com/css2?family=PT+Sans:wght@400;700&display=swap">
<style>
  :root {
    --backdrop: #ebebeb;
    --card-dark: #1b1b1b;
    --card-light: #ffffff;
    --ink-light: #ffffff;
    --ink-dark: #1b1b1b;
  }
  html, body {
    margin: 0;
    padding: 0;
    width: 1200px;
    height: 900px;
    overflow: hidden;
    background: var(--backdrop);
    font-family: "PT Sans", Arial, sans-serif;
  }
  .canvas {
    position: relative;
    width: 1200px;
    height: 900px;
  }
  .card {
    position: absolute;
    width: 347px;
    height: 560px;
    background: var(--card-dark);
    overflow: hidden;
  }
  .card-front { left: 237px; top: 170px; }
  .card-back { left: 649px; top: 170px; }

  .front-brand {
    height: 245px;
    background: var(--card-light);
    display: flex;
    align-items: center;
    justify-content: center;
  }
  .brand-name {
    margin: 0;
    font-weight: 700;
    font-size: 36px;
    letter-spacing: 0.5px;
    color: var(--ink-dark);
    white-space: nowrap;
  }
  .front-details {
    color: var(--ink-light);
    padding: 34px 0 0 33px;
  }
  .person-name {
    margin: 0;
    font-size: 22px;
    font-weight: 700;
    line-height: 26px;
  }
  .person-role {
    margin: 0;
    font-size: 19px;
    line-height: 24px;
  }
  .contact-list {
    list-style: none;
    margin: 37px 0 0 0;
    padding: 0;
    font-size: 16.5px;
    line-height: 21px;
  }
  .contact-list li {
    display: flex;
    align-items: center;
  }
  .contact-icon {
    width: 11px;
    height: 11px;
    margin: 0 9px 0 2px;
    fill: var(--ink-light);
  }
  .address {
    margin: 28px 0 0 0;
    font-size: 16.5px;
    line-height: 21px;
    font-style: normal;
  }
  .back-brand {
    position: absolute;
    inset: 0;
    display: flex;
    align-items: center;
    justify-content: center;
  }
  .back-brand .brand-name {
    color: var(--ink-light);
    font-size: 38px;
  }
</style>
</head>
<body>
<main class="canvas">
  <section class="card card-front" aria-label="Business card front">
    <div class="front-brand">
      <h1 class="brand-name">Calderwell Climate</h1>
    </div>
    <div class="front-details">
      <p class="person-name">Dominic Westerhall</p>
      <p class="person-role">Director</p>
      <ul class="contact-list">
        <li>
          <svg class="contact-icon" viewBox="0 0 12 12" aria-hidden="true"><path d="M1 4 Q6 0 11 4 L9 5.5 L8 4 Q6 3.3 4 4 L3 5.5 Z M3 6 H9 L10 11 H2 Z"/></svg>
          862-415-2736
        </li>
        <li>
          <svg class="contact-icon" viewBox="0 0 12 12" aria-hidden="true"><path d="M3 1 H8 V4 H11 V11 H1 V4 H3 Z M4 2 V4 H7 V2 Z M3 6 V7 H5 V6 Z M6 6 V7 H8 V6 Z M3 8 V9 H5 V8 Z M6 8 V9 H8 V8 Z"/></svg>
          862-415-2739
        </li>
        <li>
          <svg class="contact-icon" viewBox="0 0 12 12" aria-hidden="true"><path d="M1 3 H11 L6 7 Z M1 4 L6 8 L11 4 V10 H1 Z"/></svg>
          info@calderwell.example
        </li>
        <li>
          <svg class="contact-icon" viewBox="0 0 12 12" aria-hidden="true"><circle cx="6" cy="6" r="5.5"/></svg>
          www.CalderwellLLC.example
        </li>
      </ul>
      <address class="address">PO box 518<br>Brightwater NJ 07912</address>
    </div>
  </section>

  <section class="card card-back" aria-label="Business card back">
    <div class="back-brand">
      <p class="brand-name">Calderwell Climate</p>
    </div>
  </section>
</main>
</body>
</html>
```